Existing Website Requiring new Pages

I have an existing word press website that was built using elementor.
Website: www.tallowcrestcare.com.au
I require the Vacancies page (https://www.tallowcrestcare.com.au/vacancies/) to be modified to display our new properties along with minor tweaks to how the information is presented.
The vacancies to be displayed are the exactly the same as those that are located on the homepage of QMR website (https://qmr.org.au/)
The new pages that link off the Vacancies tab will require custom design.
There are roughly 8 pages/properties to be incorporated. i wish for the design to be very similar to that displayed in the following link; https://www.polunda.com.au/vacancies/merrylands
Along with this the back end has not been updated for the last 3 years so it also requires some maintenance.
Website is in the disability industry and the custom pages will display information relative to Property Vacancies.
I have attached a ZIP file with some design guides, the information for each of the properties (which will need to be modified to show our business name Tallowcrest Care) and the example of how it is to look based off the Polunda website.
If you guys have any suggestions or ideas on how to make this more presentable or possible i'm open to your ideas.
Target Market(s)
People looking for SDA properties custom built for people with a disability
Industry/Entity Type
Disability
Coding
Coded - Design and coding required
Number of Pages Required
5+ page

```html
<!DOCTYPE html>
<html lang="en">
<head>
<meta charset="utf-8">
<title>Vacancies – Tallowcrest Care</title>
<link rel="stylesheet" href="https://fonts.googleapis.com/css2?family=Montserrat:wght@400;500;600;700&display=swap">
<style>
:root{
  --ink:#1d1d1d;
  --muted:#8a8a8a;
  --accent:#f29a2e;
  --brand:#d9479b;
  --teal:#2bb5c9;
  --line:#e4e4e4;
  --bar:#242424;
  --white:#fff;
}
*{box-sizing:border-box;margin:0;padding:0}
html,body{width:1200px;height:2847px;overflow:hidden;background:var(--white);font-family:"Montserrat",sans-serif;color:var(--ink)}
.page{position:relative;width:1200px;height:2847px}
.brand{position:absolute;display:flex;align-items:center;gap:10px;font-weight:600;color:var(--brand);font-size:22px}
.brand .dot{width:18px;height:18px;border-radius:50%;background:var(--brand)}
.site-header .brand{left:112px;top:62px}
.nav{position:absolute;top:72px;left:500px;font-size:13.5px;font-weight:500;letter-spacing:.2px}
.nav a{position:absolute;white-space:nowrap;color:var(--ink);text-decoration:none}
.nav a.active{color:var(--accent)}
.hero{position:absolute;top:154px;left:0;width:1200px;height:466px;background:linear-gradient(90deg,#4a3a26 0%,#8a6a3a 25%,#6b5a44 45%,#7c6c5c 60%,#b44a34 75%,#3a3430 100%)}
.hero h1{position:absolute;left:112px;top:192px;font-size:68px;font-weight:700;color:var(--white)}
.card{position:absolute;width:477px;height:410px;background:var(--white);box-shadow:0 2px 10px rgba(0,0,0,.12)}
.card .photo{position:absolute;left:17px;top:18px;width:443px;height:293px;background:linear-gradient(180deg,#7fb4e6 0%,#b9d6ee 45%,#a08a70 62%,#6f9a45 80%,#5a8a3a 100%)}
.card h2{position:absolute;left:21px;top:335px;font-size:24px;font-weight:600;white-space:nowrap}
.card .beds{position:absolute;right:17px;top:340px;display:flex;align-items:center;gap:12px;font-size:15.5px;font-weight:500;white-space:nowrap}
.card .beds svg{width:32px;height:21px}
.card .arrow{position:absolute;right:18px;top:372px}
.site-footer{position:absolute;top:2490px;left:0;width:1200px;height:311px;background:var(--white);box-shadow:0 -8px 14px rgba(0,0,0,.05)}
.site-footer .brand{left:122px;top:86px}
.contact{position:absolute;left:120px;top:196px;font-size:12.5px;color:#888;line-height:22px;list-style:none}
.contact li{display:flex;align-items:center;gap:8px}
.social{position:absolute;left:523px;top:54px;list-style:none}
.social li{width:32px;height:32px;border-radius:50%;margin-bottom:9px;background:#0b4f8a}
.social li:first-child{background:#5a2b82}
.social li:nth-child(3){background:#111}
.fcol{position:absolute;top:46px;width:224px}
.fcol h3{font-size:14px;font-weight:600;border-left:3px solid var(--teal);padding-left:13px;margin-bottom:14px;line-height:14px}
.fcol ul{list-style:none}
.fcol li{font-size:12.5px;color:var(--muted);border-bottom:1px solid var(--line);padding:9px 0;line-height:22px}
.fcol li:first-child{border-top:1px solid var(--line)}
.bottom-bar{position:absolute;left:0;top:2801px;width:1200px;height:46px;background:var(--bar);color:var(--white);font-size:12.5px;text-align:center;line-height:46px}
</style>
</head>
<body>
<div class="page">
  <header class="site-header">
    <div class="brand"><span class="dot"></span>Tallowcrest Care</div>
    <nav class="nav">
      <a style="left:0">HOME</a>
      <a style="left:66px">ABOUT US</a>
      <a class="active" style="left:160px">WHAT WE DO <svg width="14" height="9" viewBox="0 0 14 9"><path d="M1 1l6 6 6-6" fill="none" stroke="#f29a2e" stroke-width="1.6"/></svg></a>
      <a style="left:289px">REFERRALS</a>
      <a style="left:398px">FEEDBACK</a>
      <a style="left:499px">CONTACT US</a>
    </nav>
  </header>

  <section class="hero" role="img" aria-label="Smiling woman in a red jacket seated in a wheelchair outdoors among autumn trees">
    <h1>Vacancies</h1>
  </section>

  <main>
    <article class="card" style="left:112px;top:706px"><div class="photo" role="img" aria-label="Two-storey brick house in Penrith"></div><h2>Penrith</h2><div class="beds"><svg viewBox="0 0 34 22" fill="none" stroke="#333" stroke-width="1.5"><path d="M2 2v19M32 10v11M2 15h30M2 10h30M6 10V5h9v5M18 10V5h9v5"/></svg>4 Bedroom SIL Home</div><svg class="arrow" width="26" height="14" viewBox="0 0 26 14" fill="none" stroke="#999" stroke-width="1.4"><path d="M0 7h24M18 1l6 6-6 6"/></svg></article>
    <article class="card" style="left:612px;top:706px"><div class="photo" role="img" aria-label="Timber cottage with ramp in Mount Druitt"></div><h2>Mount Druitt</h2><div class="beds"><svg viewBox="0 0 34 22" fill="none" stroke="#333" stroke-width="1.5"><path d="M2 2v19M32 10v11M2 15h30M2 10h30M6 10V5h9v5M18 10V5h9v5"/></svg>4 Bedroom SIL Home</div><svg class="arrow" width="26" height="14" viewBox="0 0 26 14" fill="none" stroke="#999" stroke-width="1.4"><path d="M0 7h24M18 1l6 6-6 6"/></svg></article>
    <article class="card" style="left:112px;top:1135px"><div class="photo" role="img" aria-label="Single-storey cream brick house in Casula"></div><h2>Casula</h2><div class="beds"><svg viewBox="0 0 34 22" fill="none" stroke="#333" stroke-width="1.5"><path d="M2 2v19M32 10v11M2 15h30M2 10h30M6 10V5h9v5M18 10V5h9v5"/></svg>4 Bedroom SIL Home</div><svg class="arrow" width="26" height="14" viewBox="0 0 26 14" fill="none" stroke="#999" stroke-width="1.4"><path d="M0 7h24M18 1l6 6-6 6"/></svg></article>
    <article class="card" style="left:612px;top:1135px"><div class="photo" role="img" aria-label="Dark timber house with chimneys in Eastwood"></div><h2>Eastwood</h2><div class="beds"><svg viewBox="0 0 34 22" fill="none" stroke="#333" stroke-width="1.5"><path d="M2 2v19M32 10v11M2 15h30M2 10h30M6 10V5h9v5M18 10V5h9v5"/></svg>4 Bedroom SIL Home</div><svg class="arrow" width="26" height="14" viewBox="0 0 26 14" fill="none" stroke="#999" stroke-width="1.4"><path d="M0 7h24M18 1l6 6-6 6"/></svg></article>
    <article class="card" style="left:112px;top:1562px"><div class="photo" role="img" aria-label="Brick house with double garage and palm tree in Baulkham Hills"></div><h2>Baulkham Hills</h2><div class="beds"><svg viewBox="0 0 34 22" fill="none" stroke="#333" stroke-width="1.5"><path d="M2 2v19M32 10v11M2 15h30M2 10h30M6 10V5h9v5M18 10V5h9v5"/></svg>4 Bedroom SIL Home</div><svg class="arrow" width="26" height="14" viewBox="0 0 26 14" fill="none" stroke="#999" stroke-width="1.4"><path d="M0 7h24M18 1l6 6-6 6"/></svg></article>
    <article class="card" style="left:612px;top:1562px"><div class="photo" role="img" aria-label="Red brick house with long driveway in Merrylands"></div><h2>Merrylands</h2><div class="beds"><svg viewBox="0 0 34 22" fill="none" stroke="#333" stroke-width="1.5"><path d="M2 2v19M32 10v11M2 15h30M2 10h30M6 10V5h9v5M18 10V5h9v5"/></svg>4 Bedroom SIL Home</div><svg class="arrow" width="26" height="14" viewBox="0 0 26 14" fill="none" stroke="#999" stroke-width="1.4"><path d="M0 7h24M18 1l6 6-6 6"/></svg></article>
    <article class="card" style="left:112px;top:1990px"><div class="photo" role="img" aria-label="Large colonial homestead on lawn in Parramatta"></div><h2>Parramatta</h2><div class="beds"><svg viewBox="0 0 34 22" fill="none" stroke="#333" stroke-width="1.5"><path d="M2 2v19M32 10v11M2 15h30M2 10h30M6 10V5h9v5M18 10V5h9v5"/></svg>4 Bedroom SIL Home</div><svg class="arrow" width="26" height="14" viewBox="0 0 26 14" fill="none" stroke="#999" stroke-width="1.4"><path d="M0 7h24M18 1l6 6-6 6"/></svg></article>
    <article class="card" style="left:612px;top:1990px"><div class="photo" role="img" aria-label="White weatherboard house with veranda in Cabramatta"></div><h2>Cabramatta</h2><div class="beds"><svg viewBox="0 0 34 22" fill="none" stroke="#333" stroke-width="1.5"><path d="M2 2v19M32 10v11M2 15h30M2 10h30M6 10V5h9v5M18 10V5h9v5"/></svg>4 Bedroom SIL Home</div><svg class="arrow" width="26" height="14" viewBox="0 0 26 14" fill="none" stroke="#999" stroke-width="1.4"><path d="M0 7h24M18 1l6 6-6 6"/></svg></article>
  </main>

  <footer class="site-footer">
    <div class="brand"><span class="dot"></span>Tallowcrest Care</div>
    <ul class="contact">
      <li><svg width="13" height="10" viewBox="0 0 13 10" fill="none" stroke="#e0356a" stroke-width="1.3"><rect x=".7" y=".7" width="11.6" height="8.6"/><path d="M1 1l5.5 4.5L12 1"/></svg>Email: info@tallowcrestcare.com.au</li>
      <li><svg width="13" height="13" viewBox="0 0 13 13"><path d="M3 1l2 3-1.3 1.5c.8 1.7 2 2.9 3.7 3.7L9 8l3 2-1 2.5C5.5 12 1 7.5.5 2z" fill="#e0356a"/></svg>Phone: +61 0400 555 182</li>
      <li><svg width="13" height="13" viewBox="0 0 13 13" fill="none" stroke="#e0356a" stroke-width="1.3"><circle cx="6.5" cy="6.5" r="5.7"/><path d="M6.5 3v3.5l2.3 1.5"/></svg>Operating Hours: 9AM To 5PM Monday - Friday</li>
    </ul>
    <ul class="social" aria-label="Social links"><li></li><li></li><li></li><li></li></ul>
    <div class="fcol" style="left:614px">
      <h3>ACCOMMODATION</h3>
      <ul><li>Supported Independent Living (SIL)</li><li>Specialist Disability Accommodation (SDA)</li><li>Short term Accommodation (Respite)</li><li>Vacancies</li></ul>
    </div>
    <div class="fcol" style="left:862px">
      <h3>WHAT WE DO</h3>
      <ul><li style="padding:5px 0">In Home Care</li><li style="padding:5px 0">Social &amp; Community Services</li><li style="padding:5px 0">Therapeutic Supports</li><li style="padding:5px 0">Support Coordination</li><li style="padding:5px 0">Home Modifications</li></ul>
    </div>
  </footer>
  <div class="bottom-bar">© Copyright 2024 | Tallowcrest Care | All Rights Reserved.</div>
</div>
</body>
</html>
```